Web Design Project

Desisgn a new style for the proposed website as per the attached link. The logo will remain as is, and it is likely that the colours will be as per the attached style guide.

Otherwise look and feel, icons, layout, images are within scope.

Current prosposed home page:
http://vantrelux-newsite.pagemorrowhost.com/index

Target Market(s)

Typically, large organisations from any industry such as Airlines, banks, Govt agencies.

Could be operational executives, business improvement specialists, bsuienss analysts.

```html
<!DOCTYPE html>
<html lang="en">
<head>
<meta charset="utf-8">
<title>Vantrelux – Home</title>
<link href="https://fonts.googleapis.com/css2?family=Noto+Sans:wght@400;700&family=Oswald:wght@500;700&display=swap" rel="stylesheet">
<style>
:root{
  --top-bar:#2b4a80;
  --nav-bar:#0d3c9e;
  --ink-blue:#1a3f8f;
  --heading-blue:#1d4aa0;
  --button-navy:#2a4a7e;
  --button-bright:#0c44c4;
  --footer-band:#28467e;
  --footer-base:#0b2356;
  --body-text:#6e6e6e;
  --rule:#e2e2e2;
  --white:#ffffff;
  --link-pale:#a9c3f2;
  --dot-grey:#555555;
  --date-amber:#c3843b;
  --date-rust:#c25a3a;
  --date-rose:#b8354c;
}
*{margin:0;padding:0;box-sizing:border-box}
html,body{width:694px;height:1200px;overflow:hidden;background:var(--white)}
body{position:relative;font-family:"Noto Sans",Verdana,sans-serif;color:var(--body-text)}
.abs{position:absolute}

/* header */
.top-bar{left:0;top:0;width:694px;height:34px;background:var(--top-bar)}
.brand{left:42px;top:9px;display:flex;align-items:center;gap:5px;color:var(--white);font-size:12px;letter-spacing:.3px}
.brand-dot{width:16px;height:16px;border-radius:50%;border:1.5px solid var(--link-pale)}
.utility-links{right:30px;top:9px;display:flex;gap:9px;font-size:8px;color:var(--white)}
.main-nav{left:0;top:34px;width:694px;height:33px;background:var(--nav-bar);display:flex;align-items:center;padding-left:50px;font-size:8.5px;color:var(--white);letter-spacing:.2px}
.main-nav span.sep{margin:0 15px}

/* hero */
.hero{left:82px;top:83px;width:530px;height:315px;border-radius:3px;background:linear-gradient(100deg,#3a3a3c 0%,#7a6558 25%,#d8d2c8 55%,#c9c8cc 75%,#8a8fa6 100%)}
.hero-title{left:354px;top:128px;font-family:"Oswald",Impact,sans-serif;font-weight:700;font-size:54px;line-height:1;color:var(--ink-blue);letter-spacing:-1px;transform:scaleX(.92);transform-origin:left}
.hero-sub{left:361px;top:198px;font-family:"Oswald",Impact,sans-serif;font-weight:500;font-size:11px;color:var(--ink-blue)}
.slider-dots{left:315px;top:412px;display:flex;gap:8px}
.slider-dots i{width:14px;height:14px;border-radius:50%;background:var(--dot-grey)}
.slider-dots i.active{background:var(--button-bright)}

/* feature grid */
.feature-grid{left:38px;top:448px;width:618px;height:433px;border-top:1px solid var(--rule)}
.rule-h{left:38px;top:657px;width:618px;height:1px;background:var(--rule)}
.rule-v{top:448px;width:1px;height:433px;background:var(--rule)}
.feature{width:168px}
.feature h3{font-weight:400;font-size:13.5px;color:var(--heading-blue);white-space:nowrap;text-align:center;width:200px;margin-left:-16px;height:20px}
.feature .photo{margin-top:6px;width:168px;height:80px;border-radius:4px;box-shadow:0 1px 3px rgba(0,0,0,.35)}
.feature p{margin-top:16px;font-size:7.8px;line-height:11.5px}
.btn{display:inline-block;width:53px;height:25px;line-height:25px;text-align:center;color:var(--white);font-size:11px;border-radius:4px;background:var(--button-navy)}
.feature .btn{margin-top:10px}

/* footer band */
.footer-band{left:0;top:881px;width:694px;height:268px;background:var(--footer-band);color:var(--white)}
.footer-col{top:27px}
.footer-col h2{font-weight:400;font-size:20.5px;letter-spacing:.3px;margin-bottom:12px}
.bullets{list-style:none;font-size:8.5px}
.bullets li{height:19px;padding-left:11px;position:relative}
.bullets li::before{content:"";position:absolute;left:1px;top:4px;width:5px;height:5px;border-radius:50%;background:var(--white)}
.footer-col h4{font-weight:400;font-size:9.5px;margin:0 0 6px 6px}
.opps .bullets{margin-left:6px;margin-bottom:11px}
.footer-band .btn{background:var(--button-bright);height:26px;line-height:26px;width:53px}
.news-item{display:flex;gap:7px;margin-bottom:16px}
.date{width:33px;height:33px;border-radius:3px;text-align:center;color:var(--white);font-family:"Oswald",Impact,sans-serif}
.date b{display:block;font-size:17px;line-height:21px;font-weight:500}
.date small{display:block;font-size:7px;line-height:8px;border-top:1px solid rgba(255,255,255,.6)}
.news-text{font-size:8px;line-height:12px;color:var(--link-pale)}
.news-text strong{display:block;color:var(--white);font-size:8.7px}
.footer-base{left:0;top:1149px;width:694px;height:51px;background:var(--footer-base);color:var(--white);font-size:8px;text-align:center;line-height:51px}
</style>
</head>
<body>
<header>
  <div class="abs top-bar"></div>
  <div class="abs brand"><span class="brand-dot"></span>vantrelux</div>
  <div class="abs utility-links"><span>Support</span><span>|</span><span>FAQs</span><span>|</span><span>Sitemap</span><span>|</span><span>Help</span></div>
  <nav class="abs main-nav">
    PRODUCTS<span class="sep">|</span>SERVICES<span class="sep">|</span>SOLUTIONS<span class="sep">|</span>RESOURCES<span class="sep">|</span>CUSTOMER STORIES<span class="sep">|</span>ABOUT US<span class="sep">|</span>CONTACT
  </nav>
</header>

<section class="hero-slider">
  <div class="abs hero" role="img" aria-label="Smiling professional woman at a laptop with colleagues working in a bright office behind her"></div>
  <div class="abs hero-title">THE WORLD</div>
  <div class="abs hero-sub">OF OPPROTUNITES</div>
  <div class="abs slider-dots"><i></i><i></i><i class="active"></i></div>
</section>

<section>
  <div class="abs feature-grid"></div>
  <div class="abs rule-h"></div>
  <div class="abs rule-v" style="left:239px"></div>
  <div class="abs rule-v" style="left:447px"></div>

  <article class="abs feature" style="left:57px;top:458px">
    <h3>KNOWLEDGE MANAGMENT</h3>
    <div class="photo" role="img" aria-label="Colourful figures with speech bubbles" style="background:linear-gradient(90deg,#6fb24a,#c8394f,#8a4fb0,#3a8fd0,#e1a13a);opacity:.85"></div>
    <p>Lorem Ipsum is simply dummy text of the printing and typesetting industry. Lorem Ipsum has been the industry's.</p>
    <span class="btn">MORE</span>
  </article>
  <article class="abs feature" style="left:260px;top:458px">
    <h3>CONTINOUS IMPROVMENT</h3>
    <div class="photo" role="img" aria-label="Team meeting around a white table" style="background:linear-gradient(160deg,#8b8a7c,#cfcfc8 50%,#5a6b55)"></div>
    <p>Lorem Ipsum is simply dummy text of the printing and typesetting industry. Lorem Ipsum has been the industry's.</p>
    <span class="btn">MORE</span>
  </article>
  <article class="abs feature" style="left:469px;top:458px">
    <h3>BUSINESS TRANSFORMATION</h3>
    <div class="photo" role="img" aria-label="People standing in a training room" style="background:linear-gradient(160deg,#6e6a5c,#d4cfc0 55%,#8a8270)"></div>
    <p>Lorem Ipsum is simply dummy text of the printing and typesetting industry. Lorem Ipsum has been the industry's.</p>
    <span class="btn">MORE</span>
  </article>

  <article class="abs feature" style="left:57px;top:667px">
    <h3>SYSTEM REQUIRMENTS</h3>
    <div class="photo" role="img" aria-label="Audience seated at a conference" style="background:linear-gradient(160deg,#4d4a48,#a9a39c 50%,#3c3c44)"></div>
    <p>Lorem Ipsum is simply dummy text of the printing and typesetting industry. Lorem Ipsum has been the industry's.</p>
    <span class="btn">MORE</span>
  </article>
  <article class="abs feature" style="left:260px;top:667px">
    <h3>PROCESSING MODELS</h3>
    <div class="photo" role="img" aria-label="Presenter in front of a whiteboard with formulas" style="background:linear-gradient(90deg,#e8e8e6,#d9d8d4 45%,#2e2e34 60%,#e6e6e4)"></div>
    <p>Lorem Ipsum is simply dummy text of the printing and typesetting industry. Lorem Ipsum has been the industry's.</p>
    <span class="btn">MORE</span>
  </article>
  <article class="abs feature" style="left:469px;top:667px">
    <h3>GOVERNANCE &amp; COMPILANCE</h3>
    <div class="photo" role="img" aria-label="Executives seated at a boardroom table" style="background:linear-gradient(160deg,#b7a898,#e4e0da 50%,#9c8f84)"></div>
    <p>Lorem Ipsum is simply dummy text of the printing and typesetting industry. Lorem Ipsum has been the industry's.</p>
    <span class="btn">MORE</span>
  </article>
</section>

<footer>
  <div class="abs footer-band">
    <div class="abs footer-col" style="left:68px">
      <h2>SERVICES</h2>
      <ul class="bullets">
        <li>MDRERIT SIT AMET TINUNT AC VELOR</li>
        <li>SASSISQU DIA LORETERAPIBU AC</li>
        <li>CUITAE EC EGET TELLUS NON ET LAC</li>
        <li>FELIEUM IACULIS LACINIA ICTM ELEMEN</li>
        <li>QUAT ANTPSUM DOLOR TCOECTTUE</li>
        <li>ALIQUAM CONGUE FERMENTUM NISL</li>
        <li>MAURIS ACCUML DIAM</li>
        <li>SED IN LACUS UT ENIM ASCING ALI</li>
      </ul>
      <span class="btn" style="margin:7px 0 0 7px">MORE</span>
    </div>
    <div class="abs footer-col opps" style="left:294px">
      <h2>OPPORTUNITIES</h2>
      <h4>EU MASSISQU DIA LORETEIBU</h4>
      <ul class="bullets">
        <li>Mdrerit sit amet tinunt ac velor</li>
        <li>Sassisqu dia loreterapibu ac</li>
        <li>Cuitae ec eget tellus non et lac</li>
      </ul>
      <h4>EU MASSISQU DIA LORETEIBU</h4>
      <ul class="bullets">
        <li>Mdrerit sit amet tinunt ac velor</li>
        <li>Sassisqu dia loreterapibu ac</li>
      </ul>
      <span class="btn" style="margin:0 0 0 3px">MORE</span>
    </div>
    <div class="abs footer-col" style="left:492px">
      <h2>NEWS</h2>
      <div class="news-item"><div class="date" style="background:var(--date-amber)"><b>21</b><small>NOV</small></div><div class="news-text"><strong>Eu massisqu dia loreteibu</strong>Mdrerit sit amet tinunt ac velor<br>Sassisqu dia loreterapibu.</div></div>
      <div class="news-item"><div class="date" style="background:var(--date-rust)"><b>09</b><small>NOV</small></div><div class="news-text"><strong>Eu massisqu dia loreteibu</strong>Mdrerit sit amet tinunt ac velor<br>Sassisqu dia loreterapibu.</div></div>
      <div class="news-item"><div class="date" style="background:var(--date-rose)"><b>17</b><small>NOV</small></div><div class="news-text"><strong>Eu massisqu dia loreteibu</strong>Mdrerit sit amet tinunt ac velor<br>Sassisqu dia loreterapibu.</div></div>
      <span class="btn" style="margin-top:4px">MORE</span>
    </div>
  </div>
  <div class="abs footer-base">@2012.All Rights Reserved</div>
</footer>
</body>
</html>
```